Business card design

Hi,
I need to have a business card design based on the current logo.
If competitive I not put it out to everyone.

It can be single of double sided

Target Market(s)

Food businesses

Industry/Entity Type

Food Manufacturing

Contact Information for Business Card

Details will on card will be as follows Name = Marcus Bell Email = Marcus@PanHearth.com.au Phone = 0418563207 Address = 57 Larkin Street , Marlow Heights NSW 2891 Australia

Font styles to use
Other font styles liked:
• based on two fonts - Adelle & Museo

Requirements
Must have
• Based on the on switch concept

```html
<!DOCTYPE html>
<html lang="en">
<head>
<meta charset="utf-8">
<title>PanHearth Business Card</title>
<link rel="stylesheet" href="https://fonts.googleapis.com/css2?family=Bebas+Neue&family=Lato:wght@400;700&family=Zilla+Slab:wght@600&display=swap">
<style>
  :root {
    --stage: #1c1c1c;
    --card: #111112;
    --accent: #ec2a4e;
    --ink-light: #ffffff;
    --ink-muted: #4a3336;
    --rule: #5a5a5a;
  }
  html, body {
    margin: 0;
    padding: 0;
    width: 1200px;
    height: 900px;
    overflow: hidden;
    background: var(--stage);
  }
  .stage {
    width: 1200px;
    height: 900px;
    display: flex;
    flex-direction: column;
    align-items: center;
    justify-content: center;
    gap: 48px;
  }
  .card {
    position: relative;
    width: 640px;
    height: 366px;
    background: var(--card);
    box-shadow: 0 10px 30px rgba(0,0,0,.5);
    overflow: hidden;
  }
  .card__band {
    position: absolute;
    left: 0; right: 0; bottom: 0;
    height: 12px;
    background: var(--accent);
  }
  /* Front */
  .brand {
    position: absolute;
    left: 0; right: 0; top: 118px;
    display: flex;
    flex-direction: column;
    align-items: center;
  }
  .brand__mark {
    display: flex;
    align-items: center;
    gap: 14px;
  }
  .brand__dot {
    width: 46px;
    height: 46px;
    border-radius: 50%;
    background: var(--accent);
  }
  .brand__name {
    font-family: "Lato", sans-serif;
    font-weight: 700;
    font-size: 64px;
    letter-spacing: 1px;
    color: var(--accent);
    line-height: 1;
  }
  .brand__tagline {
    margin-top: 10px;
    margin-left: 110px;
    font-family: "Zilla Slab", serif;
    font-weight: 600;
    font-size: 19px;
    letter-spacing: .5px;
    color: var(--ink-muted);
  }
  /* Back */
  .holder {
    position: absolute;
    left: 96px;
    top: 150px;
    font-family: "Bebas Neue", sans-serif;
    font-size: 46px;
    color: var(--accent);
    line-height: 1;
    letter-spacing: .5px;
  }
  .divider {
    position: absolute;
    left: 308px;
    top: 128px;
    width: 1px;
    height: 84px;
    background: var(--rule);
  }
  .contact {
    position: absolute;
    left: 330px;
    top: 138px;
    margin: 0;
    padding: 0;
    list-style: none;
    font-family: "Lato", sans-serif;
    font-size: 17px;
    color: var(--ink-light);
  }
  .contact__item {
    display: flex;
    align-items: center;
    gap: 10px;
    height: 24px;
  }
  .contact__icon {
    width: 15px;
    height: 15px;
    flex: none;
  }
  .address {
    position: absolute;
    left: 96px;
    bottom: 52px;
    font-family: "Lato", sans-serif;
    font-size: 18px;
    color: var(--ink-light);
  }
</style>
</head>
<body>
<main class="stage">
  <section class="card card--front">
    <div class="brand">
      <div class="brand__mark">
        <span class="brand__dot"></span>
        <span class="brand__name">PanHearth</span>
      </div>
      <div class="brand__tagline">Kitchen Supply Made Simple</div>
    </div>
    <div class="card__band"></div>
  </section>

  <section class="card card--back">
    <div class="holder">Marcus Bell</div>
    <div class="divider"></div>
    <ul class="contact">
      <li class="contact__item">
        <svg class="contact__icon" viewBox="0 0 16 16" aria-hidden="true">
          <path d="M3.5 1.5l2.5 3-1.5 1.7c.8 1.8 2.3 3.3 4.2 4.2l1.7-1.5 3 2.5-1.6 2.6C6.5 13.8 2.2 9.5 1 3.1z" fill="var(--accent)"/>
        </svg>
        <span>0418563207</span>
      </li>
      <li class="contact__item">
        <svg class="contact__icon" viewBox="0 0 16 16" aria-hidden="true">
          <rect x="1" y="3" width="14" height="10" fill="var(--accent)"/>
          <path d="M1 3l7 6 7-6" fill="none" stroke="var(--card)" stroke-width="1.4"/>
        </svg>
        <span>Marcus@PanHearth.com.au</span>
      </li>
      <li class="contact__item">
        <svg class="contact__icon" viewBox="0 0 16 16" aria-hidden="true">
          <g fill="none" stroke="var(--accent)" stroke-width="1.4">
            <circle cx="8" cy="8" r="6.5"/>
            <ellipse cx="8" cy="8" rx="3" ry="6.5"/>
            <path d="M1.5 8h13M2.5 5h11M2.5 11h11"/>
          </g>
        </svg>
        <span>www.PanHearth.com.au</span>
      </li>
    </ul>
    <div class="address">57 Larkin Street, Marlow Heights, NSW 2891 Australia</div>
    <div class="card__band"></div>
  </section>
</main>
</body>
</html>
```